Electronics Recycling and IT Asset Disposition Flyer and Brochure Design

We need a 2 side A5 Flyer and 4 side A4 folder( brochure) for our electronics waste recycling and IT asset management and disposition business.
Our business provides free electronics waste recycling for companies, schools, learning institutions,councils, IT companies and government sectors. Many people are ignorant of responsible recycling of electronics which could harm our health if not treated properly.
The list of other services attached in the pdf.
We provide an end to end and tailored solution for our customers from collection, logistics, data sanitisation, remarketing and recycling.

The Flyer should create awareness of responsible electronics recycling and drive the audience to contact us or go to our website to learn more about the company and services.A brief list of services should also be included in the flyer.The goal is to get the audience to contact us to enquire more about our services.

The Brochure should include all the above plus provide more details about the company, processes, services,contact details (fb, linkedin,Twitter). The goal is to convert the audience to customers for recycling and provide other services as added services.

The final design for both flyer and brochure should communicate responsible recycling of electronic scrap and tailored solution for every organisation.

The company website is www.kelvane-scrap.com.au based in Australia. We serve clients nationwide.

Target Market(s)

IT companies, Corporate, schools and learning institutions, government sector

Industry/Entity Type

Recycling

Contact Information for Business Card

Name: Harold Pendrake
email: harold@kelvane-scrap.com.au
website: www.kelvane-scrap.com.au
mobile: +614 612 39057
Phone: 1300 46 2735

Font styles to use
Serif

Requirements
Must have
• I would like the designs to have more images and icons
Nice to have
Should not have
• none

```html
<!DOCTYPE html>
<html lang="en">
<head>
<meta charset="utf-8">
<title>Kelvane Scrap – Service Offering Flyer</title>
<link rel="stylesheet" href="https://fonts.googleapis.com/css2?family=Didact+Gothic&family=Source+Sans+3:wght@600;700&display=swap">
<style>
  :root {
    --green: #5bb446;
    --green-mid: #149447;
    --green-dark: #0e3d22;
    --grey-bar: #6f6f6f;
    --band: #f0f0f0;
    --ink: #222222;
    --page-bg: #e9ebe9;
    --white: #ffffff;
  }
  * { margin: 0; padding: 0; box-sizing: border-box; }
  html, body { width: 1040px; height: 1200px; overflow: hidden; }
  body { background: var(--page-bg); position: relative; font-family: "Didact Gothic", sans-serif; }

  .flyer {
    position: absolute; left: 197px; top: 187px;
    width: 669px; height: 865px;
    background: var(--white);
    box-shadow: 0 6px 18px rgba(0,0,0,.18);
    overflow: hidden;
  }
  .top-tab { position: absolute; left: 265px; top: 0; width: 163px; height: 8px; background: var(--green); }
  .rule { position: absolute; left: 0; top: 117px; width: 100%; height: 3px; background: var(--green); }

  .hero {
    position: absolute; left: 0; top: 120px; width: 100%; height: 291px;
    background: linear-gradient(160deg, #3b4a3c 0%, #6f8a6c 35%, #3f5a3f 60%, #556b4e 100%);
  }
  .hero-band {
    position: absolute; left: 0; top: 230px; width: 100%; height: 61px;
    background: linear-gradient(90deg, rgba(70,160,60,.85), rgba(91,180,70,.9));
  }
  .hero-title {
    position: absolute; left: 0; top: 164px; width: 100%; text-align: center;
    font-family: "Source Sans 3", sans-serif; font-weight: 600; font-size: 41px;
    color: var(--white); text-shadow: 0 2px 4px rgba(0,0,0,.45);
  }
  .service-icons {
    position: absolute; top: 356px; left: 0; width: 100%; height: 48px;
  }
  .service-icons .chip {
    position: absolute; top: 0; width: 48px; height: 48px; border-radius: 50%;
    background: var(--white); display: flex; align-items: center; justify-content: center;
  }

  .brand {
    position: absolute; left: 272px; top: 23px; width: 145px; height: 145px;
    border-radius: 50%; background: var(--white); border: 2px solid var(--green);
    display: flex; align-items: center; justify-content: center; text-align: center;
    z-index: 2;
  }
  .brand-name {
    font-family: "Source Sans 3", sans-serif; font-weight: 700; font-size: 23px;
    line-height: 1.05; color: var(--green-mid);
  }

  .service { position: absolute; left: 0; width: 100%; text-align: center; }
  .service-title {
    font-family: "Source Sans 3", sans-serif; font-weight: 600; font-size: 21px;
    color: var(--green); text-decoration: underline; text-underline-offset: 3px;
  }
  .service-badge {
    width: 52px; height: 52px; margin: 0 auto; border-radius: 50%;
    background: var(--white); border: 2px solid var(--green);
    display: flex; align-items: center; justify-content: center;
  }
  .service-copy { font-size: 13px; line-height: 15.8px; color: var(--ink); }

  .collection { top: 420px; }
  .collection .band { position: absolute; left: 0; top: 61px; width: 100%; height: 142px; background: var(--band); }
  .collection .service-title, .collection .service-badge, .collection .service-copy { position: relative; }
  .collection .service-badge { margin-top: 15px; }
  .collection .service-copy { margin-top: 15px; }

  .audit { top: 642px; }
  .audit .service-badge { margin-top: 14px; }
  .audit .service-copy { margin-top: 15px; }

  .footer-bar { position: absolute; left: 0; bottom: 0; width: 100%; height: 12px; display: flex; }
  .footer-bar span:nth-child(1) { width: 36px; background: var(--green); }
  .footer-bar span:nth-child(2) { width: 88px; background: var(--green-mid); }
  .footer-bar span:nth-child(3) { width: 108px; background: var(--green-dark); }
  .footer-bar span:nth-child(4) { flex: 1; background: var(--grey-bar); }

  .ico { stroke: var(--green); fill: none; stroke-width: 2.2; stroke-linecap: round; stroke-linejoin: round; }
</style>
</head>
<body>
<svg width="0" height="0" style="position:absolute">
  <defs>
    <symbol id="i-recycle" viewBox="0 0 32 32">
      <path d="M13 6 L16 3 L19 6 M16 3 L16 3 M12 8 L7 17 M20 8 L25 17 M9 24 L23 24 M22 21 L25 24 L22 27 M5 20 L7 17 L10 18"/>
      <path d="M15 4 L10 12 M17 4 L22 12"/>
    </symbol>
    <symbol id="i-form" viewBox="0 0 32 32">
      <rect x="6" y="4" width="18" height="24" rx="2"/>
      <path d="M10 10 H20 M10 15 H20 M10 20 H15 M18 24 L27 15 L29 17 L20 26 Z"/>
    </symbol>
    <symbol id="i-data" viewBox="0 0 32 32">
      <ellipse cx="14" cy="8" rx="9" ry="3.5"/>
      <path d="M5 8 V22 C5 24 9 25.5 14 25.5 M23 8 V14 M5 15 C5 17 9 18.5 14 18.5"/>
      <circle cx="23" cy="23" r="5"/><path d="M23 20.5 V23 H25"/>
    </symbol>
    <symbol id="i-cycle" viewBox="0 0 32 32">
      <circle cx="16" cy="16" r="12"/>
      <path d="M10 15 A6 6 0 0 1 21 13 M22 10 V14 H18 M22 17 A6 6 0 0 1 11 19 M10 22 V18 H14"/>
    </symbol>
    <symbol id="i-tools" viewBox="0 0 32 32">
      <path d="M6 26 L18 14 M20 6 A5 5 0 0 0 26 12 L23 15 L17 9 Z M26 26 L14 14 M6 6 L10 6 L12 10 L10 12 L6 10 Z"/>
    </symbol>
    <symbol id="i-play" viewBox="0 0 32 32">
      <circle cx="16" cy="16" r="9"/>
      <path d="M16 3 V6 M16 26 V29 M3 16 H6 M26 16 H29 M7 7 L9 9 M23 23 L25 25 M7 25 L9 23 M23 9 L25 7"/>
      <path d="M14 12 L20 16 L14 20 Z"/>
    </symbol>
  </defs>
</svg>

<main class="flyer">
  <div class="top-tab"></div>

  <div class="hero" role="img" aria-label="Close-up photograph of a green circuit board with chips, resistors and capacitors">
    <div class="hero-band"></div>
    <h1 class="hero-title">Service Offering</h1>
    <div class="service-icons">
      <div class="chip" style="left:124px"><svg class="ico" width="30" height="30"><use href="#i-recycle"/></svg></div>
      <div class="chip" style="left:201px"><svg class="ico" width="30" height="30"><use href="#i-form"/></svg></div>
      <div class="chip" style="left:280px"><svg class="ico" width="30" height="30"><use href="#i-data"/></svg></div>
      <div class="chip" style="left:355px"><svg class="ico" width="30" height="30"><use href="#i-cycle"/></svg></div>
      <div class="chip" style="left:429px"><svg class="ico" width="30" height="30"><use href="#i-tools"/></svg></div>
      <div class="chip" style="left:500px"><svg class="ico" width="30" height="30"><use href="#i-play"/></svg></div>
    </div>
  </div>

  <div class="rule"></div>

  <div class="brand"><span class="brand-name">Kelvane<br>Scrap</span></div>

  <section class="service collection">
    <div class="band"></div>
    <h2 class="service-title">Secure E-Waste Collection Service</h2>
    <div class="service-badge"><svg class="ico" width="30" height="30"><use href="#i-recycle"/></svg></div>
    <p class="service-copy">
      Kelvane Scrap collects electronic waste from schools, businesses, home users and government departments<br>
      Secure collection includes pick up of e-waste and transportation to our recycling facility in a<br>
      secured truck<br>
      Registration of assets and reporting
    </p>
  </section>

  <section class="service audit">
    <h2 class="service-title">Receipting Registration, Test and Audit Services</h2>
    <div class="service-badge"><svg class="ico" width="30" height="30"><use href="#i-form"/></svg></div>
    <p class="service-copy">
      Registering your assets on our Asset Management System<br>
      Test, audit and verify specifications, condition and resale value Provide a detailed asset report<br>
      Cleaning and removal of company logos and asset tags
    </p>
  </section>

  <div class="footer-bar"><span></span><span></span><span></span><span></span></div>
</main>
</body>
</html>
```